Construction Company

Design a clutter free business card, it can be double-sided utilizing the logo for VKM Ltd simple with all relevant contact information.

Please also a letterhead design to function for the purposes of invoicing, all mail requirements, with header to be distinctive while the footer ties page together and incorporates all necessary information.

For now, please use generic / dummy text and when a winner is selected, I will disclose the contact information.

Hi Designers! Please read the updated brief which includes the design of a business card and letterhead. Thank you!

```html
<!DOCTYPE html>
<html lang="en">
<head>
<meta charset="utf-8">
<title>VKM Ltd Business Card</title>
<link rel="stylesheet" href="https://fonts.googleapis.com/css2?family=Arimo:wght@400;700&display=swap">
<style>
  :root {
    --backdrop: #2b2b2b;
    --card: #ffffff;
    --gold: #a8870f;
    --gold-soft: #d9c37a;
    --navy: #1a2a8c;
  }
  * { box-sizing: border-box; margin: 0; padding: 0; }
  html, body {
    width: 1200px; height: 801px; overflow: hidden;
    background: var(--backdrop);
    font-family: "Arimo", Arial, sans-serif;
  }
  .card {
    position: absolute; top: 274px;
    width: 443px; height: 263px;
    background: var(--card); overflow: hidden;
  }
  .card--front { left: 153px; }
  .card--back { left: 625px; }

  .holder { position: absolute; left: 24px; top: 28px; }
  .holder__name { color: var(--gold); font-weight: 700; font-size: 15.5px; line-height: 17px; letter-spacing: 0.1px; }
  .holder__title { color: var(--navy); font-size: 13.5px; line-height: 16px; }

  .contacts { position: absolute; left: 24px; top: 129px; list-style: none; }
  .contacts li {
    display: flex; align-items: center; gap: 6px;
    color: var(--navy); font-size: 13px; line-height: 15.6px;
  }
  .contacts svg { width: 11px; height: 11px; flex: none; fill: var(--gold); }

  .address {
    position: absolute; left: 24px; top: 205px;
    color: var(--navy); font-size: 13px; line-height: 15.6px; font-style: normal;
  }

  .brand-decoration {
    position: absolute; left: 183px; top: 4px;
    width: 260px; height: 260px; border-radius: 50%;
    background: radial-gradient(circle, var(--gold-soft) 0%, rgba(217,195,122,0.35) 60%, rgba(217,195,122,0) 72%);
  }

  .wordmark {
    position: absolute; left: 0; right: 0; top: 0; bottom: 0;
    display: flex; align-items: center; justify-content: center; gap: 10px;
  }
  .wordmark__dot { width: 14px; height: 14px; border-radius: 50%; background: var(--gold); }
  .wordmark__name { color: var(--navy); font-weight: 700; font-size: 44px; letter-spacing: 1px; }
</style>
</head>
<body>
  <section class="card card--front">
    <div class="holder">
      <p class="holder__name">JONATHAN SMITH</p>
      <p class="holder__title">Managing Director</p>
    </div>
    <ul class="contacts">
      <li><svg viewBox="0 0 12 12"><path d="M2.5 1l2 2-1 1.3a6 6 0 0 0 4.2 4.2L9 7.5l2 2-1.5 1.5C5 11 1 7 1 2.5z"/></svg>044-123 456 789</li>
      <li><svg viewBox="0 0 12 12"><path d="M3 0.5h6v11H3zM4 1.5v8h4v-8z"/></svg>044-123 456 789</li>
      <li><svg viewBox="0 0 12 12"><path d="M0 2.5h12v7H0zM1 3.2L6 7l5-3.8z" fill-rule="evenodd"/></svg>info@webname.com</li>
      <li><svg viewBox="0 0 12 12"><path d="M6 .5a5.5 5.5 0 1 0 0 11 5.5 5.5 0 0 0 0-11zm0 1c.8 0 1.6 1.6 1.8 4H4.2C4.4 3.1 5.2 1.5 6 1.5zM1.5 6.5h1.7c.1 1.3.4 2.5.9 3.3A4.5 4.5 0 0 1 1.5 6.5zm0-1A4.5 4.5 0 0 1 4.1 2.2c-.5.8-.8 2-.9 3.3zm2.7 1h3.6c-.2 2.4-1 4-1.8 4s-1.6-1.6-1.8-4zm4.6 0h1.7a4.5 4.5 0 0 1-2.6 3.3c.5-.8.8-2 .9-3.3zm0-1c-.1-1.3-.4-2.5-.9-3.3a4.5 4.5 0 0 1 2.6 3.3z"/></svg>www.websitename.com</li>
    </ul>
    <address class="address">421, Address line goes here<br>45452,Country Name</address>
    <div class="brand-decoration" role="img" aria-label="Large gold brand symbol decoration"></div>
  </section>

  <section class="card card--back">
    <div class="wordmark">
      <span class="wordmark__dot"></span>
      <span class="wordmark__name">VKM Ltd</span>
    </div>
  </section>
</body>
</html>
```